Design a compelling Tarnwove Business Card that will drive people to my site

I want a business card that I can give to people—less to tell them who I am and more to direct them to my website. My website is a portal for Pelmor Aquatics Officials and a place for people who want to become Pelmor Aquatics Officials.
I am uploading my official company logo as well as a business card mockup that I did on my own. Please feel free to completely stray from this design.
I've included a screen recording of the homepage of my website as well.
Target Market(s)
Pelmor Aquatics Officials and people who desire to become one
Contact Information for Business Card
website url
Look and feel
Each slider illustrates characteristics of the customer's brand and the style your logo design should communicate.

```html
<!DOCTYPE html>
<html lang="en">
<head>
<meta charset="utf-8">
<title>Tarnwove Business Card</title>
<link href="https://fonts.googleapis.com/css2?family=Poppins:wght@400;600;700&display=swap" rel="stylesheet">
<style>
  :root {
    --page-bg: #e9ebf0;
    --brand-blue: #3a52a6;
    --soft-blue: #93a9df;
    --white: #ffffff;
    --ink-blue: #3a52a6;
  }
  * { margin: 0; padding: 0; box-sizing: border-box; }
  html, body {
    width: 1186px; height: 1200px; overflow: hidden;
    background: var(--page-bg);
    font-family: "Poppins", sans-serif;
  }
  .sheet {
    width: 1186px; height: 1200px;
    display: flex; flex-direction: column; align-items: center;
    justify-content: center; gap: 40px;
  }
  .card {
    position: relative; width: 960px; height: 542px;
    background: var(--brand-blue); overflow: hidden;
    box-shadow: 0 6px 18px rgba(20, 30, 70, 0.25);
  }
  .card-waves { position: absolute; inset: 0; width: 100%; height: 100%; }
  .wordmark {
    position: absolute; font-weight: 600; color: var(--white);
    letter-spacing: -1px; line-height: 1;
  }
  .card-front .wordmark { left: 40px; top: 38px; font-size: 88px; }
  .holder { position: absolute; right: 42px; top: 40px; text-align: right; }
  .holder-name { font-weight: 700; font-size: 32px; color: var(--soft-blue); line-height: 1.15; }
  .holder-title { font-weight: 400; font-size: 26px; color: var(--white); line-height: 1.3; }
  .edge-tab {
    position: absolute; right: -12px; top: 46px; width: 34px; height: 70px;
    background: var(--white); border-radius: 10px;
  }
  .contact-list {
    position: absolute; right: 44px; bottom: 44px; list-style: none;
    text-align: right; color: var(--ink-blue); font-size: 27px; line-height: 34px;
  }
  .contact-list li { display: flex; align-items: center; justify-content: flex-end; gap: 10px; }
  .contact-list svg { width: 18px; height: 18px; fill: var(--ink-blue); flex: none; }
  .card-back .wordmark {
    left: 0; right: 0; top: 248px; text-align: center; font-size: 124px;
  }
  .tagline-band {
    position: absolute; left: 140px; right: 140px; top: 398px; height: 52px;
    background: linear-gradient(90deg, rgba(147,169,223,0) 0%, rgba(147,169,223,0.45) 30%, rgba(147,169,223,0.45) 70%, rgba(147,169,223,0) 100%);
    display: flex; align-items: center; justify-content: center;
  }
  .tagline { color: var(--white); font-size: 29px; font-weight: 400; white-space: nowrap; }
</style>
</head>
<body>
<main class="sheet">
  <section class="card card-front" aria-label="Business card front">
    <svg class="card-waves" viewBox="0 0 960 542" preserveAspectRatio="none" aria-hidden="true">
      <path d="M0 200 C 120 330, 320 380, 520 330 C 700 290, 860 300, 960 350 L960 542 L0 542 Z" fill="var(--soft-blue)"/>
      <path d="M0 300 C 130 420, 330 440, 520 390 C 700 345, 860 350, 960 372 L960 384 C 860 368, 700 370, 520 420 C 320 470, 110 460, 0 360 Z" fill="var(--white)"/>
    </svg>
    <div class="wordmark">tarnwove</div>
    <div class="holder">
      <p class="holder-name">Marcus Ellery</p>
      <p class="holder-title">CEO &amp; Founder</p>
    </div>
    <div class="edge-tab"></div>
    <ul class="contact-list">
      <li>(555) 214-7390
        <svg viewBox="0 0 24 24"><path d="M6.6 10.8a15 15 0 0 0 6.6 6.6l2.2-2.2c.3-.3.7-.4 1-.2 1.1.4 2.3.6 3.6.6.6 0 1 .4 1 1V20c0 .6-.4 1-1 1A17 17 0 0 1 3 4c0-.6.4-1 1-1h3.5c.6 0 1 .4 1 1 0 1.3.2 2.5.6 3.6.1.3 0 .7-.2 1z"/></svg>
      </li>
      <li>marcus@tarnwove.com
        <svg viewBox="0 0 24 24"><path d="M2 5h20v14H2z M4 7v.4l8 5.2 8-5.2V7z" fill-rule="evenodd"/></svg>
      </li>
      <li>www.tarnwove.com
        <svg viewBox="0 0 24 24"><circle cx="12" cy="12" r="10"/></svg>
      </li>
    </ul>
  </section>

  <section class="card card-back" aria-label="Business card back">
    <div class="wordmark">tarnwove</div>
    <div class="tagline-band"><p class="tagline">Your Poolside Official’s Hub</p></div>
  </section>
</main>
</body>
</html>
```